Maple Roster Business Card for recruitment company

We are looking for a Business Card Design that incorporates our personal details and our busines name and logo. We are a specialized search consultancy that recruit Property and Construction professionals.
We would like a business card that stands out and is appealing to the Construction and Property industry as well.

Target Market(s)

people in the construction and property industry

Contact Information for Business Card

Business Name and logo

Font styles to use
Serif

Colors
0094D4
00A9DD
6FCCEA
C7EBF8
E9F6FB

Requirements
Must have
• Business name and logo as well as contact details
Should not have
• No photos of us please

```html
<!DOCTYPE html>
<html lang="en">
<head>
<meta charset="utf-8">
<title>Maple Roster Business Card</title>
<link rel="stylesheet" href="https://fonts.googleapis.com/css2?family=Lora:wght@400;500;600&display=swap">
<style>
  :root {
    --backdrop: #d2d2d2;
    --paper: #ffffff;
    --brand: #0094d4;
    --brand-bright: #00a9dd;
    --brand-sky: #6fccea;
    --brand-mist: #c7ebf8;
    --brand-wash: #e9f6fb;
    --text-dark: #2f3b42;
    --on-brand: #ffffff;
  }
  * { margin: 0; padding: 0; box-sizing: border-box; }
  html, body { width: 900px; height: 1200px; overflow: hidden; }
  body {
    background: var(--backdrop);
    font-family: "Lora", Georgia, serif;
    position: relative;
  }
  .card {
    position: absolute;
    left: 79px;
    width: 743px;
    height: 440px;
    box-shadow: 0 8px 22px rgba(0,0,0,0.28);
    overflow: hidden;
  }
  .card--front { top: 131px; background: var(--paper); }
  .card--back { top: 638px; background: var(--brand); }

  .wordmark {
    position: absolute;
    left: 0; right: 0;
    height: 80px;
    display: flex;
    align-items: center;
    justify-content: center;
    gap: 18px;
  }
  .card--front .wordmark { top: 104px; }
  .card--back .wordmark { top: 184px; }
  .wordmark__mark {
    width: 46px;
    height: 46px;
    border-radius: 50%;
    flex: none;
  }
  .card--front .wordmark__mark { background: var(--brand-sky); }
  .card--back .wordmark__mark { background: var(--brand-mist); }
  .wordmark__name {
    font-weight: 500;
    font-size: 56px;
    letter-spacing: 2px;
    line-height: 1;
    white-space: nowrap;
  }
  .card--front .wordmark__name { color: var(--brand); }
  .card--back .wordmark__name { color: var(--on-brand); }

  .person {
    position: absolute;
    right: 429px;
    top: 242px;
    text-align: right;
  }
  .person__name {
    font-weight: 600;
    font-size: 25px;
    color: var(--brand);
    line-height: 1.1;
    white-space: nowrap;
  }
  .person__role {
    font-size: 16px;
    color: var(--text-dark);
    margin-top: 4px;
    white-space: nowrap;
  }
  .divider {
    position: absolute;
    left: 365px;
    top: 240px;
    width: 2px;
    height: 66px;
    background: var(--brand-bright);
  }
  .contact {
    position: absolute;
    left: 410px;
    top: 237px;
    list-style: none;
  }
  .contact__item {
    display: flex;
    align-items: center;
    height: 24.5px;
    font-size: 16px;
    color: var(--text-dark);
    white-space: nowrap;
  }
  .contact__icon {
    width: 16px;
    height: 14px;
    margin-right: 13px;
    fill: var(--brand);
  }
  .address-band {
    position: absolute;
    left: 0; right: 0;
    top: 355px;
    height: 40px;
    background: var(--brand);
    color: var(--on-brand);
    font-size: 16px;
    display: flex;
    align-items: center;
    justify-content: center;
  }
  .footer-strip {
    position: absolute;
    left: 0; right: 0;
    top: 395px;
    bottom: 0;
    background: var(--brand-wash);
  }
</style>
</head>
<body>
  <section class="card card--front">
    <div class="wordmark">
      <span class="wordmark__mark"></span>
      <span class="wordmark__name">MAPLE ROSTER</span>
    </div>

    <div class="person">
      <div class="person__name">Dana Holloway</div>
      <div class="person__role">Owner/ Designer</div>
    </div>

    <div class="divider"></div>

    <ul class="contact">
      <li class="contact__item">
        <svg class="contact__icon" viewBox="0 0 16 14" aria-hidden="true">
          <path d="M1 5 C1 2 4 1 8 1 C12 1 15 2 15 5 L12 5 L11 3.5 L5 3.5 L4 5 Z"/>
          <path d="M4 6 L12 6 L14 13 L2 13 Z"/>
          <circle cx="8" cy="9.3" r="1.8" fill="#ffffff"/>
        </svg>
        (555) 014-2387
      </li>
      <li class="contact__item">
        <svg class="contact__icon" viewBox="0 0 16 14" aria-hidden="true">
          <path d="M2 3 L14 3 L14 4.2 L8 8 L2 4.2 Z"/>
          <path d="M2 5.6 L8 9.4 L14 5.6 L14 12 L2 12 Z"/>
        </svg>
        info@mapleroster.com
      </li>
      <li class="contact__item">
        <svg class="contact__icon" viewBox="0 0 16 14" aria-hidden="true">
          <circle cx="8" cy="7" r="6"/>
          <path d="M5 3 L8 4 L7 6.5 L4.5 7 L4 5 Z M9 8 L12 8.5 L10.5 11.5 L8.5 11 Z" fill="#ffffff"/>
        </svg>
        www.mapleroster.com
      </li>
    </ul>

    <div class="address-band">82 Harbor Lane, Cedar Point, CA 90210</div>
    <div class="footer-strip"></div>
  </section>

  <section class="card card--back">
    <div class="wordmark">
      <span class="wordmark__mark"></span>
      <span class="wordmark__name">MAPLE ROSTER</span>
    </div>
  </section>
</body>
</html>
```